Graphic- Educational Visual

Brisko Dog Training has created an educational tool to help its students understand and prioritize some key concepts in their dog training.

We are requesting a visual of this tool be designed.

Name/title of tool (to be included in graphic): The Brisko Pathway
Description: Funnel (inverted pyramid).

From top to bottom, the levels are called:

Connect
Develop
Progress
Refine

The diagram should also include a cycle around it to, to represent that one is always moving through the levels.

Business colours are included below to make sure the funnel's colours complement the website colours or at least don't clash:

#0AA1C7 Blue and #7FC31B Green
Purple as a secondary colour -75279C

For reference, business logo is attached.

Dog Training

```html
<!DOCTYPE html>
<html lang="en">
<head>
<meta charset="utf-8">
<title>The Brisko Pathway – Brisko Dog Training</title>
<link rel="stylesheet" href="https://fonts.googleapis.com/css2?family=Montserrat:wght@700;800&display=swap">
<style>
  :root {
    --brand-blue: #19a1c9;
    --brand-green: #7fc241;
    --brand-purple: #733291;
    --paper: #ffffff;
    --label: #ffffff;
  }
  html, body {
    margin: 0;
    padding: 0;
    width: 1200px;
    height: 1200px;
    overflow: hidden;
    background: var(--paper);
  }
  .pathway-diagram {
    display: block;
    width: 1200px;
    height: 1200px;
  }
  .tool-title {
    font-family: "Montserrat", sans-serif;
    font-weight: 800;
    fill: var(--brand-green);
  }
  .level-label {
    font-family: "Montserrat", sans-serif;
    font-weight: 700;
    font-size: 32px;
    letter-spacing: 0.5px;
    fill: var(--label);
  }
  .level-blue { fill: var(--brand-blue); }
  .level-green { fill: var(--brand-green); }
  .funnel-twist { fill: var(--brand-purple); }
  .cycle-arc { fill: none; stroke-width: 50; }
  .arrow-green { fill: var(--brand-green); }
  .arrow-blue { fill: var(--brand-blue); }
  .arrow-purple { fill: var(--brand-purple); }
  .icon-line { fill: none; stroke: var(--label); stroke-width: 4; stroke-linecap: round; stroke-linejoin: round; }
  .icon-fill { fill: var(--label); }
</style>
</head>
<body>
<svg class="pathway-diagram" viewBox="0 0 1500 1500" xmlns="http://www.w3.org/2000/svg" role="img" aria-label="The Brisko Pathway: a funnel of Connect, Develop, Progress and Refine inside a continuous cycle">
  <defs>
    <linearGradient id="fade-green" gradientUnits="userSpaceOnUse" x1="0" y1="1000" x2="0" y2="790">
      <stop offset="0" stop-color="#7fc241" stop-opacity="0"/>
      <stop offset="1" stop-color="#7fc241" stop-opacity="1"/>
    </linearGradient>
    <linearGradient id="fade-blue" gradientUnits="userSpaceOnUse" x1="800" y1="420" x2="1030" y2="560">
      <stop offset="0" stop-color="#19a1c9" stop-opacity="0"/>
      <stop offset="1" stop-color="#19a1c9" stop-opacity="1"/>
    </linearGradient>
    <linearGradient id="fade-purple" gradientUnits="userSpaceOnUse" x1="1085" y1="1120" x2="880" y2="1250">
      <stop offset="0" stop-color="#733291" stop-opacity="0"/>
      <stop offset="1" stop-color="#733291" stop-opacity="1"/>
    </linearGradient>
  </defs>

  <!-- Title -->
  <g class="title-block">
    <text class="tool-title" x="545" y="290" font-size="70">The Brisko</text>
    <text class="tool-title" x="962" y="344" font-size="46" text-anchor="end">Pathway</text>
  </g>

  <!-- Cycle -->
  <g class="cycle">
    <path class="cycle-arc" stroke="url(#fade-green)" d="M 347 978 A 422 422 0 0 1 752 426"/>
    <polygon class="arrow-green" points="750,373 806,428 750,484"/>

    <path class="cycle-arc" stroke="url(#fade-blue)" d="M 799 429 A 422 422 0 0 1 1113 1059"/>
    <polygon class="arrow-blue" points="1161,1086 1065,1032 1083,1111"/>

    <path class="cycle-arc" stroke="url(#fade-purple)" d="M 1071 1119 A 422 422 0 0 1 383 1059"/>
    <polygon class="arrow-purple" points="335,1087 431,1032 353,1007"/>
  </g>

  <!-- Funnel -->
  <g class="funnel">
    <polygon class="funnel-twist" points="780,731 1028,731 780,803 500,803"/>
    <polygon class="funnel-twist" points="780,875 966,875 780,948 563,948"/>
    <polygon class="funnel-twist" points="780,1020 903,1020 780,1092 626,1092"/>

    <g class="level level-connect">
      <polygon class="level-blue" points="438,659 1059,659 1028,731 469,731"/>
      <g class="icon-link" transform="translate(656,694) rotate(-45)">
        <rect class="icon-line" x="-17" y="-6" width="18" height="12" rx="6"/>
        <rect class="icon-line" x="-1" y="-6" width="18" height="12" rx="6"/>
      </g>
      <text class="level-label" x="687" y="705">CONNECT</text>
    </g>

    <g class="level level-develop">
      <polygon class="level-green" points="500,803 997,803 966,875 531,875"/>
      <path class="icon-fill" d="M659 856 L642 839 C634 831 640 822 649 822 C654 822 657 825 659 828 C661 825 664 822 669 822 C678 822 684 831 676 839 Z"/>
      <text class="level-label" x="692" y="850">DEVELOP</text>
    </g>

    <g class="level level-progress">
      <polygon class="level-blue" points="563,948 934,948 903,1020 594,1020"/>
      <polyline class="icon-line" points="638,997 647,982 653,988 662,973"/>
      <polygon class="icon-fill" points="655,970 665,968 663,978"/>
      <text class="level-label" x="675" y="995">PROGRESS</text>
    </g>

    <g class="level level-refine">
      <polygon class="level-green" points="626,1092 871,1092 840,1164 657,1164"/>
      <g class="icon-gears">
        <circle class="icon-line" cx="674" cy="1135" r="7"/>
        <circle class="icon-line" cx="674" cy="1135" r="2"/>
        <circle class="icon-line" cx="688" cy="1118" r="5"/>
        <path class="icon-line" d="M674 1124 V1127 M674 1143 V1146 M663 1135 H666 M682 1135 H685 M688 1110 V1112 M688 1124 V1126 M680 1118 H682 M694 1118 H696"/>
      </g>
      <text class="level-label" x="708" y="1140">REFINE</text>
    </g>
  </g>
</svg>
</body>
</html>
```